Construction Company

Design a clutter free business card, it can be double-sided utilizing the logo for VKM Ltd simple with all relevant contact information.

Please also a letterhead design to function for the purposes of invoicing, all mail requirements, with header to be distinctive while the footer ties page together and incorporates all necessary information.

For now, please use generic / dummy text and when a winner is selected, I will disclose the contact information.

Hi Designers! Please read the updated brief which includes the design of a business card and letterhead. Thank you!

```html
<!DOCTYPE html>
<html lang="en">
<head>
<meta charset="utf-8">
<title>VKM Ltd – Business Card</title>
<link href="https://fonts.googleapis.com/css2?family=Open+Sans:wght@400;700&display=swap" rel="stylesheet">
<style>
  :root {
    --card-blue: #263b8a;
    --gold: #b48a2c;
    --white: #ffffff;
    --backdrop: #2a2a2c;
  }
  * { margin: 0; padding: 0; box-sizing: border-box; }
  html, body { width: 1200px; height: 900px; overflow: hidden; }
  body {
    background: var(--backdrop);
    font-family: "Open Sans", sans-serif;
    display: flex;
    flex-direction: column;
    align-items: center;
    justify-content: center;
    gap: 48px;
  }
  .card {
    width: 700px;
    height: 400px;
    background: var(--card-blue);
    position: relative;
    box-shadow: 0 10px 30px rgba(0,0,0,.45);
  }
  .brand {
    display: flex;
    align-items: center;
    gap: 16px;
    color: var(--white);
    font-weight: 700;
    white-space: nowrap;
  }
  .brand-dot {
    border-radius: 50%;
    background: var(--gold);
    flex: none;
  }
  /* back side */
  .card-back { display: flex; align-items: center; justify-content: center; }
  .card-back .brand { font-size: 76px; }
  .card-back .brand-dot { width: 36px; height: 36px; }
  /* front side */
  .card-front { display: flex; align-items: center; padding: 0 50px; }
  .card-front .brand { font-size: 50px; width: 300px; }
  .card-front .brand-dot { width: 24px; height: 24px; }
  .divider {
    width: 1.5px;
    height: 200px;
    background: var(--gold);
    margin: 0 30px 0 10px;
  }
  .contact { color: var(--white); font-size: 17px; line-height: 1.45; }
  .contact-name {
    color: var(--gold);
    font-weight: 700;
    font-size: 21px;
    letter-spacing: .5px;
    text-transform: uppercase;
  }
  .contact-role { margin-bottom: 4px; }
  .contact-address { margin-bottom: 6px; }
  .contact-line { display: flex; align-items: center; gap: 8px; }
  .contact-line svg { width: 14px; height: 14px; fill: var(--gold); flex: none; }
</style>
</head>
<body>
  <section class="card card-back">
    <div class="brand"><span class="brand-dot"></span>VKM Ltd</div>
  </section>

  <section class="card card-front">
    <div class="brand"><span class="brand-dot"></span>VKM Ltd</div>
    <div class="divider"></div>
    <div class="contact">
      <p class="contact-name">Daniel Harlow</p>
      <p class="contact-role">President</p>
      <p class="contact-address">1840 Harbor View Drive<br>Seacliff CA 90210</p>
      <p class="contact-line">
        <svg viewBox="0 0 16 16" aria-hidden="true"><path d="M3.6 1.2l2.3 2.6-1.3 1.9c.9 2 2.5 3.6 4.5 4.6l1.9-1.3 2.6 2.3-1.5 2.6C6.7 13.7 2.3 9.3 1 3.8z"/></svg>
        555-240-0187
      </p>
      <p class="contact-line">
        <svg viewBox="0 0 16 16" aria-hidden="true"><path d="M1 3h14v10H1zM2.5 4.5L8 9l5.5-4.5z" fill-rule="evenodd"/></svg>
        dharlow@vkmltd.com
      </p>
      <p class="contact-line">
        <svg viewBox="0 0 16 16" aria-hidden="true"><path d="M8 1a7 7 0 100 14A7 7 0 008 1zm0 1.5c.9 1 1.5 2.5 1.7 4.5H6.3C6.5 5 7.1 3.5 8 2.5zM6.3 9h3.4c-.2 2-.8 3.5-1.7 4.5-.9-1-1.5-2.5-1.7-4.5zM2.6 7a5.5 5.5 0 012.7-4 9 9 0 00-1 4zm0 2h1.7a9 9 0 001 4 5.5 5.5 0 01-2.7-4zm8.1 4a9 9 0 001-4h1.7a5.5 5.5 0 01-2.7 4zm1-6a9 9 0 00-1-4 5.5 5.5 0 012.7 4z"/></svg>
        www.vkmltd.com
      </p>
    </div>
  </section>
</body>
</html>
```